Business Cards for new orthopaedic surgery practice

My husband and I are starting our own orthopaedic surgery practice. We are looking for a business card that is uniform, but one will have my name/title and the other will have his. You can just create one design with my name on it for now. But when I choose your design as the winning design I will ask that you add another copy with his name/title.

We are looking for classy, simple, elite all in one. We like dark blues/a little gold/yellow. Something that goes with our logo. We want our logo incorporated. Here is all the info you need:
Business name: RV Bone & Vitality Center
Location: 38517 North Willowmere Ave
Maple Hollow, FL 33990
Phone: 954-218-4063
Fax: 954-582-7341
Email: info@myrvbonecare.example

Names: Lydia Vance, M.D.
Board Certified Hand and Upper Extremity Surgeon

Ebo Dansu, M.D.
Board Certified Hip & Knee Replacement/General Orthopaedic Surgeon

Can decide what you want to put on the back. Maybe a slogan:
Grounded in Care. Centered on You

I am just going to upload our logo. The only thing is if we select you as the winning design, the location, and phone numbers may change. We will need your help to update that once fully solidified.

Industry/Entity Type

Medical

Contact Information for Business Card

Colors
0054AA
0677BA
7BADD7
CADEEF
E8F1F8
0094D4
00A9DD
6FCCEA
C7EBF8
E9F6FB

Requirements
Must have
• class, appeal,
Should not have
• We want to air on the side of masculine if we are looking at masculine vs. feminine feel. But we still want it classy, sophisticated, and something we will love

```html
<!DOCTYPE html>
<html lang="en">
<head>
<meta charset="utf-8">
<title>RV Bone &amp; Vitality Center – Business Card</title>
<link rel="stylesheet" href="https://fonts.googleapis.com/css2?family=Cinzel:wght@500;600;700&family=Poppins:wght@400;500&display=swap">
<style>
  :root {
    --page-bg: #ebebeb;
    --navy-deep: #080f2b;
    --navy: #0b1536;
    --band: #0f1c49;
    --brand-blue: #2c4b9e;
    --cyan: #1cc0e6;
    --white: #ffffff;
    --gold-dark: #a87a06;
    --gold-light: #f9d97a;
    --ink: #0a1330;
  }
  * { box-sizing: border-box; margin: 0; padding: 0; }
  html, body {
    width: 997px; height: 1200px; overflow: hidden;
    background: var(--page-bg);
  }
  .card {
    position: absolute;
    left: 110px; width: 777px; height: 443px;
    background: radial-gradient(ellipse at 30% 40%, var(--navy) 0%, var(--navy-deep) 100%);
    overflow: hidden;
  }
  .card--front { top: 129px; }
  .card--back { top: 628px; }

  .brand-name {
    font-family: "Cinzel", serif;
    font-weight: 600;
    color: var(--brand-blue);
    text-align: center;
    position: absolute; left: 0; right: 0;
    line-height: 1.2;
  }
  .card--front .brand-name { top: 150px; font-size: 40px; }
  .card--back .brand-name { top: 120px; font-size: 30px; }

  .tagline {
    position: absolute; left: 119px; top: 303px;
    width: 540px; height: 44px; border-radius: 22px;
    background: linear-gradient(90deg, var(--gold-dark) 0%, var(--gold-light) 50%, var(--gold-dark) 100%);
    font-family: "Cinzel", serif; font-weight: 700;
    font-size: 25px; color: var(--ink);
    display: flex; align-items: center; justify-content: center;
    white-space: nowrap;
  }

  .info-band {
    position: absolute; left: 3px; right: 0; top: 208px; height: 181px;
    display: flex; gap: 5px;
  }
  .info-band__panel { background: var(--band); height: 100%; }
  .info-band__panel--person { width: 386px; position: relative; }
  .info-band__panel--contact { flex: 1; position: relative; }

  .person-name {
    position: absolute; left: 81px; top: 14px;
    font-family: "Cinzel", serif; font-weight: 500;
    font-size: 31px; color: var(--cyan); white-space: nowrap;
  }
  .person-title {
    position: absolute; left: 87px; top: 65px;
    font-family: "Poppins", sans-serif; font-weight: 500;
    font-size: 20px; line-height: 25.5px; color: var(--white);
    text-transform: uppercase; white-space: nowrap;
  }

  .contact-list { list-style: none; }
  .contact-item {
    position: absolute; left: 21px;
    display: flex; align-items: flex-start; gap: 11px;
    font-family: "Poppins", sans-serif; font-weight: 400;
    font-size: 20.5px; line-height: 25px; color: var(--white);
    white-space: nowrap;
  }
  .contact-item__icon {
    width: 22px; height: 22px; flex: none; margin-top: 1px;
  }
</style>
</head>
<body>

<section class="card card--front">
  <h1 class="brand-name">RV Bone &amp; Vitality Center</h1>
  <p class="tagline">Grounded in Care. Centered on You</p>
</section>

<section class="card card--back">
  <h2 class="brand-name">RV Bone &amp; Vitality Center</h2>

  <div class="info-band">
    <div class="info-band__panel info-band__panel--person">
      <p class="person-name">Lydia Vance, M.D.</p>
      <p class="person-title">Board Certified Hand<br>and Upper Extremity<br>Surgeon</p>
    </div>

    <div class="info-band__panel info-band__panel--contact">
      <svg width="0" height="0" style="position:absolute">
        <defs>
          <linearGradient id="gold" x1="0" y1="0" x2="1" y2="1">
            <stop offset="0" stop-color="#f9d97a"/>
            <stop offset="1" stop-color="#b8860b"/>
          </linearGradient>
        </defs>
      </svg>
      <ul class="contact-list">
        <li class="contact-item" style="top:14px">
          <svg class="contact-item__icon" viewBox="0 0 22 22" aria-hidden="true">
            <circle cx="11" cy="11" r="11" fill="url(#gold)"/>
            <path d="M7.5 6.5l2 -0.5 1.2 2.6 -1.2 1c0.6 1.3 1.6 2.3 2.9 2.9l1 -1.2 2.6 1.2 -0.5 2c-4.4 0.2 -8.2 -3.6 -8 -8z" fill="#0a1330"/>
          </svg>
          <span>954-218-4063</span>
        </li>
        <li class="contact-item" style="top:45px">
          <svg class="contact-item__icon" viewBox="0 0 22 22" aria-hidden="true">
            <circle cx="11" cy="11" r="11" fill="url(#gold)"/>
            <rect x="6" y="9" width="10" height="7" rx="1" fill="#0a1330"/>
            <rect x="8" y="5.5" width="6" height="4" fill="none" stroke="#0a1330" stroke-width="1.2"/>
          </svg>
          <span>954-582-7341</span>
        </li>
        <li class="contact-item" style="top:76px">
          <svg class="contact-item__icon" viewBox="0 0 22 22" aria-hidden="true">
            <circle cx="11" cy="11" r="11" fill="url(#gold)"/>
            <rect x="6" y="7.5" width="10" height="7" rx="0.8" fill="#0a1330"/>
            <path d="M6.5 8l4.5 3.5 4.5 -3.5" fill="none" stroke="#e0b94a" stroke-width="1"/>
          </svg>
          <span>info@myrvbonecare.example</span>
        </li>
        <li class="contact-item" style="top:107px">
          <svg class="contact-item__icon" viewBox="0 0 22 22" aria-hidden="true">
            <circle cx="11" cy="11" r="11" fill="url(#gold)"/>
            <path d="M11 5a3.5 3.5 0 0 1 3.5 3.5c0 2.5 -3.5 6 -3.5 6s-3.5 -3.5 -3.5 -6A3.5 3.5 0 0 1 11 5z" fill="#0a1330"/>
            <circle cx="11" cy="8.5" r="1.2" fill="#e0b94a"/>
            <path d="M7 16h8" stroke="#0a1330" stroke-width="1.2"/>
          </svg>
          <span>38517 North Willowmere Ave<br>Maple Hollow, FL 33990</span>
        </li>
      </ul>
    </div>
  </div>
</section>

</body>
</html>
```